New Business Card Design Project

Need a design that will create an impact / strong impression towards our clients for our business. We are in the lighting business and we do lighting retrofits for large commercial to industrial clientele.

Target Market(s)

Lighting Industry

Industry/Entity Type

Business

Font styles to use
Other font styles liked:
• we would like to use the font on our logo, not sure what it is though..

Requirements
Must have
• Our logo.
Nice to have
• We are open to suggestions that have to do with lighting.

```html
<!DOCTYPE html>
<html lang="en">
<head>
<meta charset="utf-8">
<title>Brightway Retrofit Co. — Business Card</title>
<link rel="stylesheet" href="https://fonts.googleapis.com/css2?family=Open+Sans:wght@400;600;700&display=swap">
<style>
  :root {
    --page-bg: #d9d6d3;
    --card-bg: #151515;
    --card-edge: #222222;
    --green-dark: #1d5a26;
    --green-mid: #238a3a;
    --green-light: #5cc35a;
    --text-white: #f2f2f2;
    --text-grey: #9a9a9a;
    --divider: #6a6a6a;
  }
  * { box-sizing: border-box; margin: 0; padding: 0; }
  html, body {
    width: 1200px;
    height: 864px;
    overflow: hidden;
    background: var(--page-bg);
    font-family: "Open Sans", Arial, sans-serif;
  }
  .canvas {
    width: 1200px;
    height: 864px;
    display: flex;
    flex-direction: column;
    align-items: center;
    justify-content: center;
    gap: 48px;
  }
  .card {
    width: 620px;
    height: 354px;
    background: var(--card-bg);
    border: 1px solid var(--card-edge);
    position: relative;
    box-shadow: 0 6px 18px rgba(0, 0, 0, 0.25);
  }

  /* Front */
  .card-front .brand {
    position: absolute;
    left: 150px;
    top: 110px;
    display: flex;
    align-items: center;
    gap: 14px;
  }
  .brand-square {
    width: 22px;
    height: 22px;
    background: var(--green-mid);
  }
  .brand-name {
    font-weight: 700;
    font-size: 34px;
    color: var(--green-mid);
    letter-spacing: 0.5px;
  }
  .card-front .website {
    position: absolute;
    left: 150px;
    top: 200px;
    font-size: 15px;
    color: var(--text-grey);
    letter-spacing: 1.5px;
  }

  /* Back */
  .card-back .brand-mark {
    position: absolute;
    left: 40px;
    top: 152px;
    width: 290px;
    font-weight: 700;
    font-size: 30px;
    line-height: 1.15;
    color: var(--green-mid);
  }
  .card-back .divider {
    position: absolute;
    left: 352px;
    top: 60px;
    width: 1px;
    height: 234px;
    background: linear-gradient(to bottom, transparent, var(--divider), transparent);
  }
  .contact {
    position: absolute;
    left: 376px;
    top: 66px;
    color: var(--text-white);
    font-size: 15px;
    line-height: 1.38;
  }
  .contact-name {
    font-weight: 600;
    font-size: 18px;
    color: var(--green-mid);
    text-transform: uppercase;
  }
  .contact-title {
    font-weight: 600;
    font-size: 15px;
    color: var(--green-mid);
    margin-bottom: 6px;
  }
  .contact-address { margin-bottom: 4px; }
  .contact-line {
    display: flex;
    align-items: center;
    gap: 8px;
  }
  .contact-line svg {
    width: 12px;
    height: 12px;
    flex: none;
    fill: var(--green-dark);
  }
  .contact-line.plain { padding-left: 20px; }
</style>
</head>
<body>
<main class="canvas">

  <section class="card card-front" aria-label="Card front">
    <div class="brand">
      <span class="brand-square"></span>
      <span class="brand-name">Brightway Retrofit Co.</span>
    </div>
    <p class="website">www.brightwayretrofit.com</p>
  </section>

  <section class="card card-back" aria-label="Card back">
    <div class="brand-mark">Brightway Retrofit Co.</div>
    <div class="divider"></div>
    <div class="contact">
      <p class="contact-name">Daniel Reyes</p>
      <p class="contact-title">CEO/FOUNDER</p>
      <p class="contact-address">1420 Cedar Hollow Road<br>Juneau, Alaska 99801</p>
      <p class="contact-line">
        <svg viewBox="0 0 12 12" aria-hidden="true"><path d="M2 1h3l1 3-1.5 1a7 7 0 0 0 2.5 2.5L8 6l3 1v3a1 1 0 0 1-1 1A9 9 0 0 1 1 2a1 1 0 0 1 1-1z"/></svg>
        555 214 7730
      </p>
      <p class="contact-line">
        <svg viewBox="0 0 12 12" aria-hidden="true"><rect x="3" y="0.5" width="6" height="11" rx="1"/></svg>
        555 381 6042
      </p>
      <p class="contact-line">
        <svg viewBox="0 0 12 12" aria-hidden="true"><rect x="1" y="3" width="10" height="7"/><rect x="3" y="1" width="6" height="2"/></svg>
        555 907 2215
      </p>
      <p class="contact-line">
        <svg viewBox="0 0 12 12" aria-hidden="true"><circle cx="6" cy="6" r="5"/></svg>
        hello@brightwayretrofit.com
      </p>
      <p class="contact-line plain">www.brightwayretrofit.com</p>
    </div>
  </section>

</main>
</body>
</html>
```